In need of an AWESOME website for our Water Re-filling Store

The project is to design a website for our retail store front with the website www.quellbrookfillhouse.com. Currently if you go to that site it redirects you to our other site www.quellbrookbottleworks.com which is just our water bottle website. So, I need a new website created for www.quellbrookfillhouse.com (retail storefront)
Use our Squarespace to create a site with pages to help educate, tell about us, link to our water bottle brand site that is already created with Squarespace, and show the family and community aspects that we believe in. Our current water bottle website is www.quellbrookbottleworks.com for reference
We also sell hydration products, especially PRZQ products and have access to digital media through our PRZQ dealer site. we sell bottles, dispensers and other supplies for water refilling customers. We sell Ice as well.

Target Market(s)

Local residents looking to fill up their 1-5 gallon water jugs

Industry/Entity Type

Alkaline and Purified Water Retail Re-filling Store

Coding

Coded - Design and coding required

Font styles to use
Serif
Sans Serif

Colors
0054AA
0677BA
7BADD7
CADEEF
E8F1F8

Requirements
Must have
• pictures of our family in the about us section and pictures of our store inside and out.

```html
<!DOCTYPE html>
<html lang="en">
<head>
<meta charset="utf-8">
<title>Quellbrook Fill House</title>
<link href="https://fonts.googleapis.com/css2?family=Ubuntu:wght@400;500&family=Open+Sans:wght@400;600&family=Noto+Serif:wght@600&display=swap" rel="stylesheet">
<style>
  :root{
    --navy:#0e1a33;
    --indigo:#2b3f98;
    --brand:#0054AA;
    --button:#0677BA;
    --sky:#7BADD7;
    --mist:#CADEEF;
    --frost:#E8F1F8;
    --text:#3a4658;
    --white:#ffffff;
  }
  *{box-sizing:border-box;margin:0;padding:0}
  html,body{width:1200px;height:4542px;overflow:hidden;background:#f4f7fb}
  body{position:relative;font-family:"Open Sans",sans-serif;color:var(--text)}
  .page{position:absolute;left:21px;top:14px;width:1156px;height:4520px;border-radius:38px;
    background:linear-gradient(180deg,#b7d5f1 0%,#bcd8f1 40%,#d3e4f3 75%,#e3eef8 100%);
    box-shadow:0 2px 10px rgba(40,80,130,.15);overflow:hidden}
  .abs{position:absolute}
  .heading{font-family:"Ubuntu",sans-serif;font-weight:400;color:var(--navy);line-height:1.2}
  .heading .accent{color:var(--indigo)}
  .copy{font-size:15.5px;line-height:28px;color:var(--text)}
  .copy p+p{margin-top:16px}
  .btn{position:absolute;display:flex;align-items:center;justify-content:center;border-radius:26px;font-size:15px;text-decoration:none}
  .btn-primary{background:linear-gradient(180deg,#1e8ad0,var(--button));color:var(--white);box-shadow:0 3px 8px rgba(6,80,140,.3)}
  .btn-outline{background:var(--white);color:var(--navy);box-shadow:0 3px 8px rgba(6,80,140,.18)}
  .brand-name{font-family:"Ubuntu",sans-serif;font-weight:500;color:var(--brand);font-size:19px;line-height:1.1;display:flex;align-items:center;gap:8px}
  .brand-dot{width:22px;height:22px;border-radius:50%;background:var(--brand);flex:none}
  .brand-phone{font-family:"Noto Serif",serif;font-weight:600;font-size:13px;color:var(--brand)}
  .nav a{position:absolute;top:73px;font-size:15px;color:var(--navy);text-decoration:none}
  .nav-underline{position:absolute;left:-10px;top:24px}
  .photo-circle{position:absolute;border-radius:50%}
  .splash{position:absolute;left:50px;width:1060px;border-radius:50%;
    background:radial-gradient(ellipse at 50% 50%,rgba(255,255,255,.85) 0%,rgba(123,173,215,.75) 35%,rgba(6,119,186,.35) 60%,rgba(202,222,239,0) 75%)}
  .card{position:absolute;border-radius:28px;background:linear-gradient(180deg,#dbe8f5,#e6eef7);
    border:3px solid rgba(255,255,255,.7);box-shadow:0 6px 14px rgba(40,80,130,.22);padding:28px 30px}
  .card-icon{width:77px;height:77px;border-radius:50%;background:var(--sky);display:flex;align-items:center;justify-content:center}
  .card h3{font-family:"Ubuntu",sans-serif;font-weight:500;font-size:19px;color:var(--navy);margin:20px 0 12px}
  .card p{font-size:15px;line-height:28.5px;color:var(--text)}
  .gallery-tile{position:absolute;border-radius:14px}
  .footer-nav a{position:absolute;top:4199px;font-size:15px;color:var(--navy);text-decoration:none}
  .social{position:absolute;top:4320px;width:42px;height:42px;border-radius:50%;background:var(--indigo)}
  .copyright{position:absolute;left:95px;top:4400px;width:973px;height:49px;border-radius:25px;background:var(--button);color:var(--white);font-size:15px;display:flex;align-items:center;justify-content:center}
</style>
</head>
<body>
<div class="page">
  <!-- header -->
  <div class="abs" style="left:91px;top:50px">
    <div class="brand-name"><span class="brand-dot"></span>Quellbrook<br>Fill House</div>
    <div class="brand-phone" style="margin:6px 0 0 8px">555-014-2290</div>
  </div>
  <nav class="nav">
    <a style="left:353px">Home
      <svg class="nav-underline" width="68" height="14" viewBox="0 0 68 14"><path d="M2 10 Q34 0 66 8" stroke="var(--brand)" stroke-width="2.5" fill="none"/></svg></a>
    <a style="left:437px">About</a>
    <a style="left:520px">Products</a>
    <a style="left:624px">Community</a>
    <a style="left:747px">Visit Us</a>
  </nav>
  <a class="btn btn-primary" style="left:914px;top:47px;width:154px;height:46px">Visit Us Today</a>

  <!-- hero -->
  <h1 class="heading abs" style="left:91px;top:175px;font-size:52px">Clean Water.<br>Strong <span class="accent">Community.</span></h1>
  <div class="copy abs" style="left:91px;top:325px;width:450px">At Quellbrook Fill House, we provide high-quality water refilling, hydration products, and everyday essentials—served with a focus on family, trust, and community.</div>
  <a class="btn btn-primary" style="left:91px;top:474px;width:166px;height:48px">Visit Our Store</a>
  <a class="btn btn-outline" style="left:276px;top:474px;width:163px;height:48px">Get Directions</a>
  <div class="photo-circle" style="left:592px;top:150px;width:440px;height:440px;background:#6ea3e6"></div>
  <div class="photo-circle" role="img" aria-label="Storefront exterior with shop sign and glass entrance doors" style="left:636px;top:155px;width:428px;height:428px;background:linear-gradient(180deg,#b9a37d 0%,#a48e68 45%,#2c2f36 60%,#55585e 100%)"></div>

  <div class="splash" role="img" aria-label="Water splash illustration" style="top:592px;height:450px"></div>

  <!-- about -->
  <div class="photo-circle" role="img" aria-label="Family portrait of the store owners and their children" style="left:106px;top:1023px;width:440px;height:440px;background:linear-gradient(180deg,#6ea3e6 0%,#7fb0e8 55%,#e9e4dc 80%,rgba(232,241,248,0) 100%)"></div>
  <h2 class="heading abs" style="left:576px;top:1100px;font-size:37px">About <span class="accent">Quellbrook Fill House</span></h2>
  <div class="copy abs" style="left:576px;top:1160px;width:500px">
    <p>Quellbrook Fill House was built with a simple goal—to provide clean, reliable water while creating a place our community can count on every day.</p>
    <p>As a family-owned business, we believe hydration should be easy, affordable, and accessible to everyone. That's why we've created a clean, welcoming space where customers can refill water, find quality hydration products, and feel confident in what they're getting.</p>
  </div>
  <a class="btn btn-primary" style="left:578px;top:1423px;width:165px;height:48px">Learn More</a>
  <a class="btn btn-outline" style="left:766px;top:1423px;width:176px;height:48px">Visit Us Today</a>

  <!-- products -->
  <h2 class="heading abs" style="left:0;width:1156px;text-align:center;top:1625px;font-size:38px">Our Products <span class="accent">&amp; Services</span></h2>
  <div class="card" style="left:91px;top:1745px;width:290px;height:393px">
    <div class="card-icon"><svg width="36" height="36" viewBox="0 0 24 24"><path d="M12 2 C8 8 5 11 5 15 a7 7 0 0 0 14 0 C19 11 16 8 12 2z" fill="var(--indigo)"/></svg></div>
    <h3>Clean Water Refilling</h3>
    <p>Our water refill stations are designed to provide high-quality, great-tasting water you can trust. Whether you're filling up for home or on the go, we make the process quick, easy, and affordable.</p>
  </div>
  <div class="card" style="left:415px;top:1720px;width:323px;height:380px">
    <div class="card-icon"><svg width="38" height="38" viewBox="0 0 24 24" fill="var(--indigo)"><rect x="3" y="12" width="8" height="8" rx="1.5"/><rect x="13" y="12" width="8" height="8" rx="1.5"/><rect x="8" y="3" width="8" height="8" rx="1.5"/></svg></div>
    <h3>Fresh Ice</h3>
    <p>We offer convenient ice options perfect for everyday use, events, or staying prepared. Stop in and grab what you need—fast and hassle-free.</p>
  </div>
  <div class="card" style="left:778px;top:1745px;width:290px;height:393px">
    <div class="card-icon"><svg width="38" height="38" viewBox="0 0 24 24" fill="var(--indigo)"><rect x="6" y="2" width="6" height="3" rx="1"/><rect x="4" y="6" width="10" height="16" rx="2"/><rect x="15" y="14" width="6" height="8" rx="1"/></svg></div>
    <h3>Hydration &amp; Electrolytes</h3>
    <p>We carry a selection of hydration products, including electrolyte mixes like PRZQ, to help support energy, recovery, and daily wellness. Whether you're active we've got you covered.</p>
  </div>
  <a class="btn btn-primary" style="left:489px;top:2152px;width:172px;height:48px">Visit Us Today</a>

  <div class="splash" role="img" aria-label="Water splash illustration" style="top:2212px;height:380px;left:80px;width:1010px"></div>

  <!-- gallery -->
  <h2 class="heading abs" style="left:0;width:1156px;text-align:center;top:2620px;font-size:38px">Inside Quellbrook Fill House</h2>
  <div class="gallery-tile" role="img" aria-label="Store wall display of water jugs, bottles and dispensers" style="left:95px;top:2708px;width:313px;height:419px;background:linear-gradient(180deg,#3f7fc8 0%,#1c1f26 25%,#2a2c33 70%,#5b6d8a 100%)"></div>
  <div class="gallery-tile" role="img" aria-label="Outdoor event tent selling alkaline and purified water" style="left:424px;top:2708px;width:312px;height:203px;background:linear-gradient(180deg,#1f3f8a 0%,#2f4f9a 45%,#8a9bb0 100%)"></div>
  <div class="gallery-tile" role="img" aria-label="Merchandise table with water bottles at a community event" style="left:424px;top:2924px;width:312px;height:203px;background:linear-gradient(180deg,#b03038 0%,#6e5a63 40%,#1e2d6a 100%)"></div>
  <div class="gallery-tile" role="img" aria-label="Owners standing behind rows of bottled water in the store" style="left:757px;top:2708px;width:311px;height:419px;background:linear-gradient(180deg,#dcd7c8 0%,#8a7a66 50%,#c9c6c0 75%,#8f7a5a 100%)"></div>
  <a class="btn btn-primary" style="left:471px;top:3171px;width:213px;height:46px">View More Gallery</a>

  <!-- visit -->
  <h2 class="heading abs" style="left:93px;top:3353px;font-size:38px">Stop By and See Us <span class="accent">Today</span></h2>
  <div class="copy abs" style="left:93px;top:3412px;width:510px">
    <p>Quellbrook Fill House was built with a simple goal—to provide clean, reliable water while creating a place our community can count on every day.</p>
    <p>As a family-owned business, we believe hydration should be easy, affordable, and accessible to everyone. That's why we've created a clean, welcoming space where customers can refill water, find quality hydration products, and feel confident in what they're getting.</p>
  </div>
  <a class="btn btn-primary" style="left:95px;top:3676px;width:166px;height:48px">Get Directions</a>
  <a class="btn btn-outline" style="left:283px;top:3676px;width:176px;height:48px">Visit Us Today</a>
  <div class="photo-circle" style="left:622px;top:3320px;width:440px;height:440px;background:#6ea3e6"></div>
  <div class="photo-circle" role="img" aria-label="Two staff members shaking hands beside the water filtration equipment" style="left:656px;top:3328px;width:430px;height:430px;background:linear-gradient(180deg,#2a56b8 0%,#3764c4 45%,#5a6c88 75%,#9aa3ae 100%)"></div>

  <div class="splash" role="img" aria-label="Water splash illustration" style="top:3800px;height:340px"></div>

  <!-- footer -->
  <div class="abs" style="left:88px;top:4185px">
    <div class="brand-name" style="font-size:21px"><span class="brand-dot"></span>Quellbrook<br>Fill House</div>
    <div class="brand-phone" style="margin:6px 0 0 14px;font-size:15px">555-014-2290</div>
  </div>
  <div class="social" style="left:104px" role="img" aria-label="Social profile link"></div>
  <div class="social" style="left:157px" role="img" aria-label="Social profile link"></div>
  <div class="social" style="left:208px" role="img" aria-label="Social profile link"></div>
  <nav class="footer-nav">
    <a style="left:337px">HOME</a>
    <a style="left:415px">ABOUTUS</a>
    <a style="left:517px">PRODUCTS &amp; SERVICES</a>
    <a style="left:715px">COMMUNITY</a>
    <a style="left:840px">VISIT US</a>
  </nav>
  <div class="heading abs" style="left:337px;top:4244px;font-size:38px">Stay hydrated. Stay connected.</div>
  <div class="copy abs" style="left:337px;top:4294px;width:540px;font-size:15px">Family-owned and committed to providing reliable hydration solutions you can trust every day.</div>
  <a class="btn btn-primary" style="left:900px;top:4235px;width:166px;height:48px">Visit Us Today</a>
  <div class="copyright">© 2026 Quellbrook Fill House. All rights reserved.</div>
</div>
</body>
</html>
```